Mortgage Company ready to make a statement!

We have a basic logo that I am fairly happy with ... but it could use a little bit of tweaking before we order the sign for our building. We also want some knock-your-socks-off business cards.
Problem: Inside of our Mortgage Office (Bright Fern Mortgage Group), we are going to have a coffee lounge (Sunbrew Cafe) for Realtors to use instead of the local Cuppington to meet with homebuyers. The office and coffee lounge are in an industrial building and is decorated with cozy overstuffed chairs, a hodge podge of interesting lamps and furniture, and goal is to make it as inviting as possible. However, we are a financial institution... so we need to keep it pretty clean as well.
One of my favorite marketing ideas is to cut a house key for everyone who buys a home using us with a key that matches our logo. There's only one key shape that works really well, so that needs to match the logo in order for the idea to work. I'll attach an image of the key blank.... although the way the key hole cut out looks terrible, so I was thinking of having them just do a thin outline instead.
Would like a similar, matching logo for the Sunbrew Cafe... but possibly something that would be a little less formal and would be cute on a coffee mug- nothing stuffy.
AND, we're opening a home inspection company as well, and we would like that logo and branding to match. The home inspection company is "Bright Fern Home Inspections"
We were thinking that for the home inspection company , we could use a magnifying glass shape inside of the house shape for the logo, use a keyhole shape inside of the same house for the mortgage company, and use a coffee cup inside of the house shape for Sunbrew Cafe.
Just getting stuck and need to help. I designed the attached logo myself, and that is what we are currently using. Designers at local printing companies have failed to impress us.
The mortgage industry has a lot of numbers and logos, etc that they require us to put on our business cards... so it's hard to keep them looking clean.
HELP! HELP! :)

```html
<!DOCTYPE html>
<html lang="en">
<head>
<meta charset="utf-8">
<title>Bright Fern Mortgage Group — Business Cards</title>
<link href="https://fonts.googleapis.com/css2?family=Marcellus&family=Montserrat:wght@400;600&display=swap" rel="stylesheet">
<style>
  :root {
    --bg: #eeece7;
    --card: #ffffff;
    --brand-blue: #1d5f80;
    --text-grey: #4a4a4a;
    --muted-grey: #5c5c5c;
    --shadow: rgba(40, 38, 34, 0.28);
  }
  html, body {
    margin: 0;
    padding: 0;
    width: 1200px;
    height: 929px;
    overflow: hidden;
    background: var(--bg);
  }
  .canvas {
    position: relative;
    width: 1200px;
    height: 929px;
  }
  .card {
    position: absolute;
    width: 580px;
    height: 332px;
    background: var(--card);
    box-shadow: 3px 5px 10px var(--shadow);
  }
  .card--front { left: 90px; top: 110px; }
  .card--back  { left: 530px; top: 480px; }

  .brand {
    display: flex;
    align-items: center;
    gap: 12px;
    font-family: "Marcellus", serif;
    color: var(--brand-blue);
    white-space: nowrap;
  }
  .brand__dot {
    border-radius: 50%;
    background: var(--brand-blue);
    flex: none;
  }
  .card--front .brand {
    position: absolute;
    left: 0; right: 0; top: 0; bottom: 0;
    justify-content: center;
    font-size: 32px;
  }
  .card--front .brand__dot { width: 22px; height: 22px; }

  .card--back .brand {
    position: absolute;
    right: 36px;
    top: 36px;
    font-size: 17px;
    gap: 8px;
  }
  .card--back .brand__dot { width: 12px; height: 12px; }

  .person {
    position: absolute;
    left: 40px;
    top: 118px;
  }
  .person__name {
    font-family: "Marcellus", serif;
    font-size: 26px;
    letter-spacing: 1px;
    color: var(--brand-blue);
    text-transform: uppercase;
    margin: 0;
  }
  .person__role {
    font-family: "Montserrat", sans-serif;
    font-weight: 600;
    font-size: 16px;
    color: var(--text-grey);
    margin: 2px 0 0 18px;
  }
  .address {
    position: absolute;
    right: 40px;
    top: 140px;
    text-align: right;
    font-family: "Montserrat", sans-serif;
    font-size: 14px;
    line-height: 1.3;
    color: var(--muted-grey);
  }
  .contact {
    position: absolute;
    left: 140px;
    bottom: 36px;
    margin: 0;
    padding: 0;
    list-style: none;
    font-family: "Montserrat", sans-serif;
    font-size: 15px;
    color: var(--muted-grey);
  }
  .contact__item {
    display: flex;
    align-items: center;
    gap: 12px;
    line-height: 23px;
  }
  .contact__icon {
    width: 13px;
    height: 13px;
    flex: none;
  }
</style>
</head>
<body>
<main class="canvas">

  <section class="card card--front" aria-label="Business card front">
    <div class="brand">
      <span class="brand__dot"></span>
      <span class="brand__name">Bright Fern Mortgage Group</span>
    </div>
  </section>

  <section class="card card--back" aria-label="Business card back">
    <div class="brand">
      <span class="brand__dot"></span>
      <span class="brand__name">Bright Fern Mortgage Group</span>
    </div>

    <div class="person">
      <h1 class="person__name">Dana Whitlow</h1>
      <p class="person__role">CEO</p>
    </div>

    <address class="address" style="font-style:normal">
      Lantern Court<br>
      Sydney Melbourne
    </address>

    <ul class="contact">
      <li class="contact__item">
        <svg class="contact__icon" viewBox="0 0 13 13" aria-hidden="true">
          <rect x="3" y="0.8" width="7" height="11.4" rx="1.2" fill="none" stroke="#1d5f80" stroke-width="1.2"/>
          <line x1="5.5" y1="10.4" x2="7.5" y2="10.4" stroke="#1d5f80" stroke-width="1"/>
        </svg>
        <span>000-555-0142</span>
      </li>
      <li class="contact__item">
        <svg class="contact__icon" viewBox="0 0 13 13" aria-hidden="true">
          <rect x="3" y="0.5" width="7" height="4" fill="#1d5f80"/>
          <rect x="0.5" y="4.5" width="12" height="5.5" rx="1" fill="#1d5f80"/>
          <rect x="3" y="8" width="7" height="4.5" fill="#fff" stroke="#1d5f80" stroke-width="1"/>
        </svg>
        <span>000-555-0142</span>
      </li>
      <li class="contact__item">
        <svg class="contact__icon" viewBox="0 0 13 13" aria-hidden="true">
          <rect x="0.5" y="2.5" width="12" height="8.5" fill="#1d5f80"/>
          <polyline points="0.8,2.8 6.5,7.3 12.2,2.8" fill="none" stroke="#fff" stroke-width="1"/>
        </svg>
        <span>dana.whitlow@brightfernmg.com</span>
      </li>
    </ul>
  </section>

</main>
</body>
</html>
```